Harbor Law Stationary - Law Firm

I am looking for a designer who can help me design letterhead and envelopes consistent with our new business cards. Feel free to reach out to me directly at ned@harborlawgroup.example. Thank you!! Visit harborlawgroup.example to see our site and the attached files for creative assets.

Target Market(s)

Anyone needing a lawyer

Font styles to use
Other font styles liked:
• Adobe Caslon Pro

Requirements
Must have
• Adobe Caslon Pro font
Full color
Nice to have
• My photo on front along with 2/3 face of camo - see mock up for example of what I have in mind.

American colors - similar to the ones found on my website and gold.

```html
<!DOCTYPE html>
<html lang="en">
<head>
<meta charset="utf-8">
<title>Harbor Law Stationery</title>
<link rel="stylesheet" href="https://fonts.googleapis.com/css2?family=Libre+Caslon+Text:wght@400;700&family=Arimo:wght@400&display=swap">
<style>
:root{
  --backdrop:#7b797a;
  --navy:#0b2748;
  --gold:#b3a068;
  --paper:#ffffff;
  --ink:#3d3d3d;
  --muted:#777777;
  --rule:#2a2a2a;
  --badge:#eeeeee;
}
*{margin:0;padding:0;box-sizing:border-box}
html,body{width:1200px;height:770px;overflow:hidden;background:var(--backdrop)}
.stage{position:relative;width:1200px;height:770px}
.serif{font-family:"Libre Caslon Text",Georgia,serif}
.sans{font-family:Arimo,Helvetica,Arial,sans-serif}

/* letterhead */
.letterhead{position:absolute;left:93px;top:63px;width:457px;height:643px;background:var(--paper);box-shadow:1px 1px 3px rgba(0,0,0,.35)}
.letterhead-band{position:absolute;left:0;top:0;width:100%;height:78px;background:var(--navy)}
.brand{position:absolute;display:flex;align-items:center;gap:8px;color:var(--gold);font-weight:700;letter-spacing:.06em;text-transform:uppercase}
.brand-dot{width:10px;height:10px;border-radius:50%;background:var(--gold);flex:none}
.letterhead .brand{left:48px;top:30px;font-size:16px}
.contact{position:absolute;left:326px;top:25px;color:#fff;font-size:7.4px;line-height:9.4px}
.letter-body{position:absolute;left:48px;top:244px;width:360px;color:var(--ink)}
.salutation{font-size:9.6px;margin-bottom:9px}
.letter-body p{font-size:7.1px;line-height:10.8px;text-align:justify;margin-bottom:10.8px;color:#4a4a4a}
.closing{font-size:7.4px;margin-top:27px}
.signature{display:block;margin-top:14px;width:58px;height:22px}
.letter-foot{position:absolute;left:47px;top:588px;width:362px;height:36px}
.foot-address{position:absolute;left:3px;top:2px;font-size:7.8px;line-height:9.6px;color:var(--muted)}
.foot-services{position:absolute;right:0;top:3px;font-size:7.8px;line-height:9.6px;color:var(--muted);text-align:right}
.foot-services .sep{display:inline-block;width:3px;height:3px;border-radius:50%;background:var(--navy);vertical-align:middle;margin:0 3px}
.foot-rule{position:absolute;top:24px;height:1px;background:var(--rule)}
.foot-rule.left{left:0;width:139px}
.foot-rule.right{left:206px;width:156px}
.badges{position:absolute;left:139px;top:0;width:67px;height:36px;background:var(--badge)}

/* envelope back */
.envelope-back{position:absolute;left:644px;top:331px;width:508px;height:251px;background:var(--paper);box-shadow:1px 1px 3px rgba(0,0,0,.35)}
.envelope-flap{position:absolute;left:0;top:0;width:508px;height:81px}
.flap-mark{position:absolute;left:0;top:35px;width:100%;text-align:center;color:var(--gold);font-size:8px;font-weight:700;letter-spacing:.08em;text-transform:uppercase}

/* envelope front */
.envelope-front{position:absolute;left:584px;top:454px;width:509px;height:252px;background:var(--paper);box-shadow:1px 1px 3px rgba(0,0,0,.35)}
.envelope-band{position:absolute;left:0;top:0;width:100%;height:76px;background:var(--navy)}
.envelope-front .brand{left:31px;top:20px;font-size:16px}
.return-address{position:absolute;left:62px;top:42px;color:#fff;font-size:7.6px;line-height:9.6px}
</style>
</head>
<body>
<main class="stage">

  <section class="letterhead" aria-label="Letterhead">
    <header class="letterhead-band">
      <div class="brand serif"><span class="brand-dot"></span>Harbor Law</div>
      <div class="contact serif">
        P: (555)014-2290<br>
        E: ellen@harborlawgroup.example<br>
        W: www.harborlawgroup.example
      </div>
    </header>

    <div class="letter-body sans">
      <div class="salutation">Dear Mr. Smith,</div>
      <p>Lorem ipsum dolor sit amet, consectetur adipiscing elit. Donec orci purus, luctus vitae dignissim eu, iaculis sed purus. Vivamus faucibus, ipsum nec aliquet viverra, leo mauris condimentum ligula, sit amet sagittis enim ligula quis arcu. Nam egestas tortor id nisi porttitor mattis. In tortor ante, ultricies in suscipit a, tempus non massa. Vivamus et auctor mi. Fusce vel massa nulla. Phasellus nec eros mauris, et scelerisque orci.</p>
      <p>Donec malesuada orci vitae nulla accumsan porta a id massa. Quisque accumsan iaculis magna sit amet fringilla. Maecenas consequat, magna eget tincidunt semper, odio nibh rutrum mi, id feugiat ante nisi eu risus. Vestibulum nunc orci, rhoncus a placerat in, ultricies in mi. Cras mattis varius eros, vel fringilla nisi suscipit eget. Quisque scelerisque sagittis nulla at porttitor.</p>
      <p>Sed id augue vitae urna euismod commodo aliquet a quam. Pellentesque arcu velit, cursus et malesuada ut, consequat et diam. Nullam erat sem, rhoncus id ullamcorper vitae, rhoncus et arcu. In ultricies ultricies nulla, ut rutrum nisi iaculis at. Donec eu magna a metus ornare faucibus. Fusce aliquet faucibus ultricies. Morbi semper, est id tincidunt gravida, sem arcu adipiscing lacus, ac bibendum nulla leo eu purus. Quisque nec diam sed risus consectetur a ccumsan quis quis nibh. Vestibulum id purus lorem.</p>
      <div class="closing">Sincerely,</div>
      <svg class="signature" role="img" aria-label="Handwritten signature" viewBox="0 0 58 22">
        <rect x="0" y="6" width="58" height="10" fill="var(--navy)" opacity=".12"/>
      </svg>
    </div>

    <footer class="letter-foot serif">
      <div class="foot-address">48 Quay Street<br>Bayport, Florida 32099</div>
      <div class="foot-rule left"></div>
      <div class="badges">
        <svg width="67" height="36" viewBox="0 0 67 36" aria-hidden="true">
          <circle cx="17" cy="16" r="12" fill="none" stroke="#2f5aa8" stroke-width="1.5"/>
          <circle cx="48" cy="16" r="13" fill="#d8b43a" stroke="var(--navy)" stroke-width="2"/>
        </svg>
      </div>
      <div class="foot-rule right"></div>
      <div class="foot-services">
        Personal Injury<span class="sep"></span>Injunctions<br>
        Criminal Defense<span class="sep"></span>Family Law
      </div>
    </footer>
  </section>

  <section class="envelope-back" aria-label="Envelope back">
    <svg class="envelope-flap" viewBox="0 0 508 81" aria-hidden="true">
      <path d="M0 0 H508 L498 55 Q492 81 466 81 H42 Q16 81 12 55 Z" fill="var(--navy)"/>
    </svg>
    <div class="flap-mark serif">Harbor Law</div>
  </section>

  <section class="envelope-front" aria-label="Envelope front">
    <header class="envelope-band">
      <div class="brand serif"><span class="brand-dot"></span>Harbor Law</div>
      <div class="return-address serif">48 Quay Street<br>Bayport, Florida 32099</div>
    </header>
  </section>

</main>
</body>
</html>
```